TheKindFrame.net

TheKindFRame.net
Live World Art Gallery of pictures of love for all to enjoy
My goal is to create a website that is designed to be an online art gallery of photos that display what love looks like from all over the world. People will submit an image; write a short quote about why their image represents love
I Love THIS website:
http://petermarlow.example/
Please create something like this!!!
User Functionality:
Users must be able to do the following:
• Upload one photo
• Write a brief quote
• Share on their social media site
• Other users can like and share posted image
Backend:
• Site owner must be able to choose which images are uploaded. After user uploads image to site, admin will receive notice of the upload, and make sure the image is not unappropriated or spam. That would be the control functionality.
• At the bottom of the site a contact us, that will send e-mail to admin for any user related questions
Design Functionality:
Website should only be one, simple, elegant, page of photos.
Social Media:
Social media buttons should be small, at the corner of each submitted image
I Love THIS website:
http://petermarlow.example/
Homepage: I like the layout and design you have now. Each square/image will have the following social media options, friendhub,chirpr,and Snapgrid. Below each photo their will be a caption that described each photo that appears after you hover over the photo, camera equipment, and a link to the photographer's portfolio/website. There will be able 30-40 images at a time on the homepage, 5-7 photographers at a time.
Featured Photographers:
This is the second page of the website. Here there is a bio of the photographers, how to contact them, and where in the world they are from. The photographers will always be on the page even after their work is taken off the homepage. I will insert links to their personal websites under their bio.
Review/Shop:
Here I will be using affiliated marketing to sell cameras, camera accessories, online photo classes, frames. I will not be selling the pictures featured on the homepage, people will be able to buy directly from the photographer.
Selling: I will be using veltra partners, and tally nook. I will be installing CoinDrop, but all sales will be they third party vendors
Contact Us:
Here people can inquire about becoming a featured photographer, the company, and anything else
Site Requirements:
Email visitors can join the company mail group.
Target Market(s)
photographers, people who like snapgrid, and boardly
Industry/Entity Type
Marketing

```html
<!DOCTYPE html>
<html lang="en">
<head>
<meta charset="utf-8">
<title>TheKindFrame.net – Marina Westbrook</title>
<link rel="stylesheet" href="https://fonts.googleapis.com/css2?family=Exo+2:wght@400&family=Lobster&family=Satisfy&family=Yanone+Kaffeesatz:wght@400;500&display=swap">
<style>
  :root {
    --navy: #17415f;
    --red: #f20d0d;
    --black: #050505;
    --white: #ffffff;
    --select-bg: #e4e6e8;
    --select-arrow: #5d5f61;
    --select-text: #55606a;
    --strip: rgba(40, 40, 40, 0.75);
    --dot-a: #35506c;
    --dot-b: #c8232c;
    --dot-c: #3b5998;
    --dot-d: #1da1f2;
  }
  * { box-sizing: border-box; margin: 0; padding: 0; }
  html, body { width: 1043px; height: 1200px; overflow: hidden; }
  body {
    position: relative;
    font-family: "Yanone Kaffeesatz", sans-serif;
    background:
      radial-gradient(ellipse 420px 300px at 140px 620px, rgba(40,35,32,0.55), transparent 70%),
      radial-gradient(ellipse 380px 320px at 960px 700px, rgba(70,62,58,0.5), transparent 70%),
      radial-gradient(ellipse 240px 160px at 940px 940px, rgba(30,50,80,0.45), transparent 70%),
      linear-gradient(180deg, #f3f5f8 0px, #eef1f4 300px, #d6d2cc 400px, #9a9189 520px, #7b736d 700px, #847d78 900px, #6f6964 1095px);
  }
  .account-bar {
    position: absolute; inset: 0 0 auto 0; height: 47px;
    background: var(--white);
    box-shadow: 0 3px 8px rgba(0,0,0,0.12);
    font-family: "Exo 2", sans-serif; font-size: 18px; color: var(--navy);
  }
  .account-bar .link { position: absolute; top: 13px; }
  .account-bar .link::after {
    content: ""; display: inline-block; margin-left: 5px; vertical-align: 3px;
    border: 5px solid transparent; border-top: 7px solid var(--navy); border-bottom: 0;
  }
  .account-bar .divider { position: absolute; left: 774px; top: 12px; width: 1px; height: 26px; background: #b9c2ca; }
  .brand {
    position: absolute; left: 177px; top: 68px;
    font-family: "Lobster", cursive; font-size: 33px; color: var(--black);
  }
  .menu {
    position: absolute; left: 787px; top: 80px;
    font-family: "Exo 2", sans-serif; font-size: 18px; color: var(--navy);
    display: flex; align-items: center; gap: 14px;
  }
  .page-title {
    position: absolute; left: 0; right: 0; top: 180px; text-align: center;
    font-family: "Satisfy", cursive; font-size: 64px; font-weight: 400; color: var(--navy);
  }
  .page-title .accent { color: var(--red); }
  .sort {
    position: absolute; top: 324px; width: 125px; height: 22px;
    background: var(--select-bg); border: 1px solid #c9ccd0;
    font-family: "Exo 2", sans-serif; font-size: 11px; color: var(--select-text);
    line-height: 20px; padding-left: 14px;
  }
  .sort::after {
    content: ""; position: absolute; right: 0; top: -1px; width: 24px; height: 22px;
    background: var(--select-arrow);
  }
  .sort::before {
    content: ""; position: absolute; right: 7px; top: 7px; z-index: 1;
    border: 5px solid transparent; border-top: 6px solid var(--white); border-bottom: 0;
  }
  .card { position: absolute; width: 175px; }
  .frame {
    position: relative; height: 179px; border: 4px solid var(--black);
    border-radius: 3px; overflow: hidden; background: var(--black);
  }
  .photo { position: absolute; inset: 0; }
  .fold {
    position: absolute; right: 0; top: 0; width: 0; height: 0;
    border-left: 30px solid transparent; border-top: 30px solid var(--black);
  }
  .heart { position: absolute; right: 5px; top: 4px; width: 14px; height: 13px; }
  .share-strip {
    position: absolute; left: 0; right: 0; bottom: 0; height: 20px;
    background: var(--strip); display: flex; justify-content: center; align-items: center; gap: 3px;
  }
  .share-strip span { width: 10px; height: 10px; border-radius: 50%; }
  .share-strip span:nth-child(1) { background: var(--dot-a); }
  .share-strip span:nth-child(2) { background: var(--dot-b); }
  .share-strip span:nth-child(3) { background: var(--dot-c); }
  .share-strip span:nth-child(4) { background: var(--dot-d); }
  .view-overlay {
    position: absolute; inset: 0; background: rgba(60,70,60,0.35);
    display: flex; align-items: center; justify-content: center;
  }
  .card-title { margin: 10px 0 0 5px; font-size: 17px; font-weight: 500; color: var(--white); }
  .card-title .accent { color: var(--red); }
  .card-text {
    margin: 3px 0 0 5px; font-size: 12px; line-height: 15px; color: var(--white); width: 170px;
  }
  .col-1 { left: 239px; } .col-2 { left: 435px; } .col-3 { left: 630px; }
  .row-1 { top: 415px; } .row-2 { top: 705px; }
  .tone-run { background: linear-gradient(160deg, #8a9a86, #6d7a63 50%, #56584b); }
  .tone-rock { background: linear-gradient(180deg, #4d8fe0 0%, #a9ccf0 40%, #a2582e 65%, #7a3f20 100%); }
  .tone-pond { background: linear-gradient(180deg, #eaf3d2 0%, #7fb23b 35%, #5d7a3c 60%, #95ad6a 100%); }
  .tone-dog { background: linear-gradient(170deg, #e9c27a 0%, #c9852f 35%, #6b4b2c 65%, #8b8f92 100%); }
  .load-more {
    position: absolute; left: 451px; top: 1002px; width: 141px; height: 37px;
    background: var(--red); border: 0; border-radius: 2px;
    font-family: "Yanone Kaffeesatz", sans-serif; font-size: 22px; font-weight: 500; color: var(--white);
  }
  .site-footer {
    position: absolute; left: 0; right: 0; top: 1095px; height: 105px; background: var(--black);
  }
  .footer-nav {
    display: flex; justify-content: center; gap: 27px; margin-top: 33px;
    font-family: "Lobster", cursive; font-size: 16px; color: var(--white); list-style: none;
  }
  .footer-social { display: flex; justify-content: center; gap: 5px; margin-top: 16px; }
  .footer-social span { width: 21px; height: 21px; border: 2px solid var(--white); border-radius: 50%; }
</style>
</head>
<body>
  <header>
    <div class="account-bar">
      <span class="link" style="left:653px">My Account</span>
      <span class="divider"></span>
      <span class="link" style="left:783px">Sign Out</span>
    </div>
    <div class="brand">TheKindFrame.net</div>
    <div class="menu">Menu
      <svg width="15" height="13" viewBox="0 0 15 13"><rect width="15" height="3" fill="#17415f"/><rect y="5" width="15" height="3" fill="#17415f"/><rect y="10" width="15" height="3" fill="#17415f"/></svg>
    </div>
  </header>

  <h1 class="page-title">Marina <span class="accent">Westbrook</span></h1>

  <div class="sort" style="left:262px">Most popular</div>
  <div class="sort" style="left:457px">Most liked</div>
  <div class="sort" style="left:651px">Most viewed</div>

  <main>
    <article class="card col-1 row-1">
      <div class="frame">
        <div class="photo tone-run" role="img" aria-label="Photo of a runner sprinting along a country road"></div>
        <div class="view-overlay">
          <svg width="50" height="30" viewBox="0 0 50 30"><path d="M2 15 Q25 -8 48 15 Q25 38 2 15Z" fill="#fff"/><circle cx="25" cy="15" r="9" fill="#17415f"/><circle cx="25" cy="15" r="4" fill="#8a9a86"/></svg>
        </div>
        <svg class="heart" viewBox="0 0 14 13"><path d="M7 13 L1 6.5 A3.4 3.4 0 0 1 7 2 A3.4 3.4 0 0 1 13 6.5 Z" fill="#f20d0d"/></svg>
        <div class="share-strip"><span></span><span></span><span></span><span></span></div>
      </div>
      <h2 class="card-title"><span class="accent">Pellentesque</span> accumsan</h2>
      <p class="card-text">Lorem ipsum is a dummy text only. Dolor sit amet, consectetur adipiscing elit.</p>
    </article>

    <article class="card col-2 row-1">
      <div class="frame">
        <div class="photo tone-rock" role="img" aria-label="Photo of a couple taking a selfie on a red rock summit"></div>
        <div class="fold"></div>
        <svg class="heart" viewBox="0 0 14 13"><path d="M7 13 L1 6.5 A3.4 3.4 0 0 1 7 2 A3.4 3.4 0 0 1 13 6.5 Z" fill="#f20d0d"/></svg>
        <div class="share-strip"><span></span><span></span><span></span><span></span></div>
      </div>
      <h2 class="card-title"><span class="accent">Pellentesque</span> accumsan</h2>
      <p class="card-text">Lorem ipsum is a dummy text only. Dolor sit amet, consectetur adipiscing elit.</p>
    </article>

    <article class="card col-3 row-1">
      <div class="frame">
        <div class="photo tone-pond" role="img" aria-label="Photo of a green garden pond with stone figures"></div>
        <div class="fold"></div>
        <svg class="heart" viewBox="0 0 14 13"><path d="M7 13 L1 6.5 A3.4 3.4 0 0 1 7 2 A3.4 3.4 0 0 1 13 6.5 Z" fill="#f20d0d"/></svg>
        <div class="share-strip"><span></span><span></span><span></span><span></span></div>
      </div>
      <h2 class="card-title"><span class="accent">Pellentesque</span> accumsan</h2>
      <p class="card-text">Lorem ipsum is a dummy text only. Dolor sit amet, consectetur adipiscing elit.</p>
    </article>

    <article class="card col-1 row-2">
      <div class="frame">
        <div class="photo tone-dog" role="img" aria-label="Photo of a father, child and dog at sunset"></div>
        <div class="fold"></div>
        <svg class="heart" viewBox="0 0 14 13"><path d="M7 13 L1 6.5 A3.4 3.4 0 0 1 7 2 A3.4 3.4 0 0 1 13 6.5 Z" fill="#f20d0d"/></svg>
        <div class="share-strip"><span></span><span></span><span></span><span></span></div>
      </div>
      <h2 class="card-title"><span class="accent">Pellentesque</span> accumsan</h2>
      <p class="card-text">Lorem ipsum is a dummy text only. Dolor sit amet, consectetur adipiscing elit.</p>
    </article>

    <article class="card col-2 row-2">
      <div class="frame">
        <div class="photo tone-rock" role="img" aria-label="Photo of a couple taking a selfie on a red rock summit"></div>
        <div class="fold"></div>
        <svg class="heart" viewBox="0 0 14 13"><path d="M7 13 L1 6.5 A3.4 3.4 0 0 1 7 2 A3.4 3.4 0 0 1 13 6.5 Z" fill="#f20d0d"/></svg>
        <div class="share-strip"><span></span><span></span><span></span><span></span></div>
      </div>
      <h2 class="card-title"><span class="accent">Pellentesque</span> accumsan</h2>
      <p class="card-text">Lorem ipsum is a dummy text only. Dolor sit amet, consectetur adipiscing elit.</p>
    </article>

    <article class="card col-3 row-2">
      <div class="frame">
        <div class="photo tone-pond" role="img" aria-label="Photo of a green garden pond with stone figures"></div>
        <div class="fold"></div>
        <svg class="heart" viewBox="0 0 14 13"><path d="M7 13 L1 6.5 A3.4 3.4 0 0 1 7 2 A3.4 3.4 0 0 1 13 6.5 Z" fill="#f20d0d"/></svg>
        <div class="share-strip"><span></span><span></span><span></span><span></span></div>
      </div>
      <h2 class="card-title"><span class="accent">Pellentesque</span> accumsan</h2>
      <p class="card-text">Lorem ipsum is a dummy text only. Dolor sit amet, consectetur adipiscing elit.</p>
    </article>
  </main>

  <button class="load-more">Load more</button>

  <footer class="site-footer">
    <ul class="footer-nav">
      <li>Home</li><li>Contact</li><li>Pinboard</li><li>Biography</li><li>Award-Exhibitions-Travels</li><li>My way of working</li>
    </ul>
    <div class="footer-social"><span></span><span></span><span></span><span></span><span></span></div>
  </footer>
</body>
</html>
```